Oversized Postcard for Estate Planning & Probate 1st 2nd and 3rd prizes

Create a professional, fresh and polished oversized post card for law firm specializing in Estate Planning & Probate Law for High Net Worth Clients

Use any picture(s) of your choice (mine or ones you recommend), logo, headshot and company info

www.morvenashbylaw.com

Westbrook Office - 4800 Kestrel Avenue, Suite 900, Charlotte, NC 28210
Harlowe Office - 13470 Birch Court, Suite 400, Charlotte, NC 28277

Phone (704) 555-0187

Use this card for a Free Consultation

Target Market(s)

young and old families too; business owners

Industry/Entity Type

Law Firm

Font styles to use
Serif
Sans Serif

Requirements
Must have
• Use any picture(s) of your choice (mine or ones you recommend), logo, headshot and company info
• www.morvenashbylaw.com
• Westbrook Office - 4800 Kestrel Avenue, Suite 900, Charlotte, NC 28210
• Harlowe Office - 13470 Birch Court, Suite 400, Charlotte, NC 28277
• Phone (704) 555-0187
• Use this card for a Free Consultation
Nice to have
• great colors and great design; like graphics with depth /shading
Should not have
• don't use too many pics - keep it simple

```html
<!DOCTYPE html>
<html lang="en">
<head>
<meta charset="utf-8">
<title>Morven Ashby Law PLLC – Revocable Trust Postcard</title>
<link rel="stylesheet" href="https://fonts.googleapis.com/css2?family=Oswald:wght@300;400;600;700&family=Roboto+Condensed:wght@400;700&display=swap">
<style>
  :root {
    --page-bg: #e6eaee;
    --blue: #2185bb;
    --blue-deep: #17628f;
    --blue-dark: #124e72;
    --blue-light: #3fb2ea;
    --blue-pale: #9fdcfb;
    --silver: #c9ccd0;
    --silver-light: #eceef0;
    --grey-text: #8a8d91;
    --white: #ffffff;
  }
  * { margin: 0; padding: 0; box-sizing: border-box; }
  html, body { width: 960px; height: 1200px; overflow: hidden; background: var(--page-bg); }
  .canvas { position: relative; width: 960px; height: 1200px; }
  .postcard { position: absolute; left: 86px; width: 788px; height: 510px; box-shadow: 0 6px 18px rgba(0,0,0,.25); }
  .postcard--front { top: 51px; }
  .postcard--back { top: 629px; }
  .postcard svg { display: block; width: 788px; height: 510px; }
  .headline { font-family: "Oswald", sans-serif; }
  .body-text { font-family: "Roboto Condensed", sans-serif; }
</style>
</head>
<body>
<main class="canvas">

  <!-- Front side -->
  <section class="postcard postcard--front" aria-label="Postcard front">
    <svg viewBox="0 0 985 638" xmlns="http://www.w3.org/2000/svg">
      <defs>
        <linearGradient id="frontBlue" x1="0" y1="0" x2="1" y2="1">
          <stop offset="0" stop-color="#2b96cc"/>
          <stop offset="1" stop-color="#1a6c9c"/>
        </linearGradient>
        <linearGradient id="deepBlue" x1="0" y1="0" x2="0" y2="1">
          <stop offset="0" stop-color="#155b85"/>
          <stop offset="1" stop-color="#2185bb"/>
        </linearGradient>
        <linearGradient id="photoTone" x1="0" y1="0" x2="1" y2="1">
          <stop offset="0" stop-color="#bfe0ee"/>
          <stop offset=".5" stop-color="#e7d3b4"/>
          <stop offset="1" stop-color="#f2efe0"/>
        </linearGradient>
        <linearGradient id="silverFade" x1="0" y1="0" x2="1" y2="0">
          <stop offset="0" stop-color="#b9bcc0"/>
          <stop offset=".5" stop-color="#f4f5f6"/>
          <stop offset="1" stop-color="#b9bcc0"/>
        </linearGradient>
        <linearGradient id="greyPanel" x1="0" y1="0" x2="1" y2="1">
          <stop offset="0" stop-color="#e4e6e8"/>
          <stop offset="1" stop-color="#c6c9cc"/>
        </linearGradient>
      </defs>

      <rect class="front-bg" width="985" height="638" fill="url(#frontBlue)"/>

      <!-- grey textured corner -->
      <polygon class="grey-panel" points="985,180 985,638 955,638 740,405" fill="url(#greyPanel)"/>

      <!-- family photo area -->
      <polygon class="photo-family" role="img" aria-label="Photo of a smiling family with two children outdoors"
        points="345,0 985,0 985,185 750,395" fill="url(#photoTone)"/>
      <polyline class="photo-frame" points="330,0 750,410 985,200" fill="none" stroke="#fff" stroke-width="10"/>

      <!-- accent triangles -->
      <polygon points="270,50 315,50 270,95" fill="#0f4a6c" opacity=".8"/>
      <polygon points="330,30 470,170 330,170" fill="var(--blue-light)"/>
      <polygon points="335,180 440,180 387,233" fill="#124e72"/>
      <g stroke="#fff" stroke-width="1" opacity=".35">
        <line x1="195" y1="0" x2="350" y2="155"/><line x1="205" y1="0" x2="360" y2="155"/>
        <line x1="215" y1="0" x2="370" y2="155"/><line x1="225" y1="0" x2="380" y2="155"/>
      </g>

      <!-- central deep blue triangle -->
      <polygon class="center-band" points="490,175 955,638 25,638" fill="url(#deepBlue)"/>
      <line x1="15" y1="638" x2="490" y2="165" stroke="#fff" stroke-width="9"/>
      <g stroke="#fff" stroke-width="1" opacity=".4">
        <line x1="60" y1="638" x2="235" y2="463"/><line x1="70" y1="638" x2="245" y2="463"/>
        <line x1="80" y1="638" x2="255" y2="463"/><line x1="90" y1="638" x2="265" y2="463"/>
      </g>

      <!-- silver & white inner triangle -->
      <polygon points="490,350 778,638 202,638" fill="url(#silverFade)"/>
      <polygon points="490,395 733,638 247,638" fill="#fff"/>

      <!-- headline -->
      <text class="headline" x="22" y="172" font-size="63" font-weight="600" fill="#fff">REVOCABLE</text>
      <text class="headline" x="24" y="268" font-size="96" font-weight="700" fill="var(--blue-pale)" stroke="#fff" stroke-width="2" letter-spacing="2">TRUST</text>
      <line x1="26" y1="296" x2="300" y2="296" stroke="#fff" stroke-opacity=".5" stroke-width="1.5"/>
      <text class="headline" x="24" y="343" font-size="26" font-weight="300" fill="#fff">BIG THING START FROM</text>
      <text class="headline" x="24" y="379" font-size="26" font-weight="300" fill="#fff">LITTLE IDEAS</text>

      <!-- website along band -->
      <text class="body-text" transform="translate(155,605) rotate(-45)" font-size="25" letter-spacing="3" fill="#fff" fill-opacity=".85">www.morvenashbylaw.com</text>

      <!-- firm name -->
      <circle cx="493" cy="497" r="40" fill="var(--blue-deep)"/>
      <line x1="370" y1="548" x2="618" y2="548" stroke="#333" stroke-width="1.5"/>
      <text class="headline" x="493" y="585" text-anchor="middle" font-size="22" font-weight="400" fill="var(--blue)" letter-spacing="1">MORVEN ASHBY LAW PLLC</text>
      <line x1="370" y1="605" x2="618" y2="605" stroke="#333" stroke-width="1.5"/>
    </svg>
  </section>

  <!-- Back side -->
  <section class="postcard postcard--back" aria-label="Postcard back">
    <svg viewBox="0 0 985 637" xmlns="http://www.w3.org/2000/svg">
      <defs>
        <linearGradient id="backBlue" x1="0" y1="0" x2="1" y2="1">
          <stop offset="0" stop-color="#2691c7"/>
          <stop offset="1" stop-color="#1b6f9f"/>
        </linearGradient>
        <linearGradient id="silverV" x1="0" y1="0" x2="1" y2="0">
          <stop offset="0" stop-color="#9fa3a7"/>
          <stop offset=".5" stop-color="#eef0f1"/>
          <stop offset="1" stop-color="#a9adb1"/>
        </linearGradient>
        <linearGradient id="ghostPhoto" x1="0" y1="0" x2="0" y2="1">
          <stop offset="0" stop-color="#f4f5f6"/>
          <stop offset="1" stop-color="#e6e8ea"/>
        </linearGradient>
        <linearGradient id="headshotTone" x1="0" y1="0" x2="0" y2="1">
          <stop offset="0" stop-color="#4a3c33"/>
          <stop offset=".6" stop-color="#d9b987"/>
          <stop offset="1" stop-color="#2a2a2e"/>
        </linearGradient>
      </defs>

      <rect width="985" height="637" fill="#fff"/>
      <rect class="contact-panel" width="613" height="637" fill="url(#backBlue)"/>

      <!-- faint background photo -->
      <rect class="photo-ghost" role="img" aria-label="Faded photo of a child playing pilot"
        x="625" y="40" width="360" height="560" fill="url(#ghostPhoto)"/>

      <!-- chevrons -->
      <polygon points="340,0 700,0 475,225" fill="url(#silverV)"/>
      <polygon points="390,0 560,0 475,85" fill="#fff"/>
      <polygon points="395,0 555,0 475,80" fill="var(--blue)"/>
      <polygon points="165,0 370,0 267,160" fill="#1c6b99"/>
      <polyline points="150,0 267,118 385,0" fill="none" stroke="#124e72" stroke-width="6"/>

      <!-- triangles -->
      <polygon points="40,30 58,48 40,48" fill="var(--blue-light)"/>
      <polygon points="30,52 72,52 30,94" fill="#124e72"/>
      <polygon points="88,32 208,152 88,152" fill="var(--blue-light)"/>
      <polygon points="88,165 190,165 139,215" fill="#124e72"/>

      <!-- headshot -->
      <rect x="43" y="243" width="195" height="214" fill="#fff" fill-opacity=".85"/>
      <rect class="headshot" role="img" aria-label="Portrait of the attorney" x="48" y="248" width="185" height="204" fill="url(#headshotTone)"/>

      <!-- offices -->
      <g fill="#fff">
        <path d="M272,242 a10,10 0 0 1 10,10 c0,8 -10,18 -10,18 s-10,-10 -10,-18 a10,10 0 0 1 10,-10z M272,248 a4,4 0 1 0 0.01,0z" fill-rule="evenodd"/>
        <path d="M272,369 a10,10 0 0 1 10,10 c0,8 -10,18 -10,18 s-10,-10 -10,-18 a10,10 0 0 1 10,-10z M272,375 a4,4 0 1 0 0.01,0z" fill-rule="evenodd"/>
      </g>
      <g class="body-text" fill="#fff">
        <text x="298" y="262" font-size="21" font-weight="700">WESTBROOK OFFICE</text>
        <text x="298" y="294" font-size="20">4800 Kestrel Avenue, Suite</text>
        <text x="298" y="326" font-size="20">900, Charlotte, NC 28210</text>
        <text x="298" y="389" font-size="21" font-weight="700">HARLOWE OFFICE</text>
        <text x="298" y="421" font-size="20">13470 Birch Court, Suite 400,</text>
        <text x="298" y="453" font-size="20">Charlotte, NC 28277</text>
      </g>

      <!-- phone & call to action -->
      <text class="headline" x="40" y="570" font-size="86" font-weight="600" fill="var(--blue-pale)" textLength="532" lengthAdjust="spacingAndGlyphs">(704) 555-0187</text>
      <text class="body-text" x="41" y="604" font-size="24" font-weight="700" fill="#fff" textLength="530" lengthAdjust="spacingAndGlyphs">USE THIS CARD FOR A FREE CONSULTATION</text>

      <!-- stamp box -->
      <rect x="825" y="17" width="143" height="140" fill="#fff" fill-opacity=".6" stroke="#999" stroke-width="2"/>
      <text class="headline" x="896" y="82" text-anchor="middle" font-size="32" font-weight="400" fill="var(--grey-text)">POSTAL</text>
      <text class="headline" x="896" y="118" text-anchor="middle" font-size="32" font-weight="400" fill="var(--grey-text)">STAMP</text>

      <!-- address lines -->
      <g stroke="#c9ccd0" stroke-width="1.2">
        <line x1="655" y1="280" x2="970" y2="280"/>
        <line x1="655" y1="312" x2="970" y2="312"/>
        <line x1="655" y1="346" x2="970" y2="346"/>
        <line x1="655" y1="382" x2="970" y2="382"/>
        <line x1="655" y1="420" x2="970" y2="420"/>
      </g>

      <!-- firm name -->
      <circle cx="848" cy="508" r="35" fill="var(--blue-deep)"/>
      <line x1="740" y1="552" x2="955" y2="552" stroke="#333" stroke-width="1.5"/>
      <text class="headline" x="848" y="587" text-anchor="middle" font-size="20" font-weight="400" fill="var(--blue)" letter-spacing="1">MORVEN ASHBY LAW PLLC</text>
      <line x1="740" y1="606" x2="955" y2="606" stroke="#333" stroke-width="1.5"/>
    </svg>
  </section>

</main>
</body>
</html>
```